Harbor Loom Floors Letterhead

Letterhead used for business reasons. It must be editable and easy to use.

Address is 2715 W. Pelican Lane Port Laurel FL 34187 - 727.382.6519

```html
<!DOCTYPE html>
<html lang="en">
<head>
<meta charset="utf-8">
<title>Harbor Loom Floors Letterhead</title>
<link href="https://fonts.googleapis.com/css2?family=Lato:wght@400;700&family=Montserrat:wght@400&family=Open+Sans:wght@400&family=Italianno&display=swap" rel="stylesheet">
<style>
  :root {
    --backdrop: #e4e4e4;
    --paper: #ffffff;
    --accent: #e08a2a;
    --ink: #1a1a1a;
    --ink-soft: #333333;
  }
  * { box-sizing: border-box; margin: 0; padding: 0; }
  html, body {
    width: 1200px;
    height: 1079px;
    overflow: hidden;
    background: var(--backdrop);
  }
  .letterhead {
    position: absolute;
    left: 232px;
    top: 20px;
    width: 735px;
    height: 1039px;
    background: var(--paper);
    box-shadow: 0 2px 10px rgba(0,0,0,0.18);
  }
  .brand-name {
    position: absolute;
    left: 37px;
    top: 84px;
    font-family: 'Lato', sans-serif;
    font-weight: 700;
    font-size: 24px;
    color: var(--ink);
    white-space: nowrap;
  }
  .contact {
    position: absolute;
    right: 37px;
    top: 80px;
    display: flex;
    align-items: center;
    font-family: 'Montserrat', sans-serif;
    font-size: 12.5px;
    color: var(--ink-soft);
  }
  .contact-phone {
    display: flex;
    align-items: center;
    gap: 5px;
  }
  .contact-phone svg { width: 11px; height: 11px; }
  .contact-divider {
    width: 2px;
    height: 31px;
    background: var(--accent);
    margin: 0 16px 0 17px;
  }
  .contact-address {
    text-align: right;
    line-height: 17px;
  }
  .salutation {
    position: absolute;
    left: 36px;
    top: 310px;
    font-family: 'Lato', sans-serif;
    font-weight: 700;
    font-size: 18.5px;
    color: var(--ink);
  }
  .letter-body {
    position: absolute;
    left: 37px;
    top: 390px;
    width: 662px;
    font-family: 'Lato', sans-serif;
    font-size: 10.9px;
    line-height: 16px;
    color: var(--ink);
    text-align: justify;
    hyphens: auto;
  }
  .letter-body p + p { margin-top: 16px; }
  .closing {
    position: absolute;
    left: 36px;
    top: 790px;
    font-family: 'Open Sans', sans-serif;
    font-size: 20px;
    color: var(--ink);
  }
  .signature {
    position: absolute;
    left: 36px;
    top: 838px;
    font-family: 'Italianno', cursive;
    font-size: 42px;
    color: var(--ink);
  }
</style>
</head>
<body>
  <main class="letterhead">
    <header>
      <div class="brand-name">Harbor Loom Floors</div>
      <div class="contact">
        <div class="contact-phone">
          <svg viewBox="0 0 24 24" aria-hidden="true"><path fill="#e08a2a" d="M6.6 10.8c1.4 2.8 3.8 5.1 6.6 6.6l2.2-2.2c.3-.3.7-.4 1-.2 1.1.4 2.3.6 3.6.6.6 0 1 .4 1 1V20c0 .6-.4 1-1 1C10.6 21 3 13.4 3 4c0-.6.4-1 1-1h3.5c.6 0 1 .4 1 1 0 1.3.2 2.5.6 3.6.1.3 0 .7-.2 1z"/></svg>
          <span>727.382.6519</span>
        </div>
        <div class="contact-divider"></div>
        <div class="contact-address">2715 W. Pelican Lane<br>Port Laurel FL 34187</div>
      </div>
    </header>

    <h1 class="salutation">Dear Mr, Alden</h1>

    <section class="letter-body">
      <p>Lorem ipsum dolor sit amet, consectetur adipiscing elit, sed do eiusmod tempor incididunt ut labore et dolore magna aliqua. Ut enim ad minim veniam, quis nostrud exercitation ullamco laboris nisi ut aliquip ex ea commodo consequat. Duis aute irure dolor in reprehenderit in voluptate velit esse cillum dolore eu fugiat nulla pariatur.Contrary to popular belief, Lorem Ipsum is not simply random text. It has roots in a piece of classical Latin literature from 45 BC, making it over 2000 years old. Edwin Calloway, a Latin professor at Ashford Hill College in Virginia, looked up one of the more obscure Latin words, consectetur, from a Lorem Ipsum passage, and going through the cites of the word in classical literature, discovered the undoubtable source.</p>
      <p>Lorem ipsum dolor sit amet, consectetur adipiscing elit, sed do eiusmod tempor incididunt ut labore et dolore magna aliqua. Ut enim ad minim veniam, quis nostrud exercitation ullamco laboris nisi ut aliquip ex ea commodo consequat. Duis aute irure dolor in reprehenderit in voluptate velit esse cillum dolore eu fugiat nulla pariatur. There are many variations of passages of Lorem Ipsum available, but the majority have suffered alteration in some form, by injected humour, or randomised words which don't look even slightly believable.</p>
      <p>Lorem ipsum dolor sit amet, consectetur adipiscing elit, sed do eiusmod tempor incididunt ut labore et dolore magna aliqua. Ut enim ad minim veniam, quis nostrud exercitation ullamco laboris nisi ut aliquip ex ea commodo consequat.Contrary to popular belief, Lorem Ipsum is not simply random text. It has roots in a piece of classical Latin literature from 45 BC, making it over 2000 years old. Edwin Calloway, a Latin professor at Ashford Hill College</p>
      <p>Excepteur sint occaecat cupidatat non proident, sunt in culpa qui officia deserunt mollit anim id est laborum. re et dolore magnam aliquam quaerat voluptatem.Contrary to popular belief, Lorem Ipsum is not simply random text. It has roots in a piece of classical Latin literature from 45 BC,</p>
    </section>

    <p class="closing">Sincerely,</p>
    <p class="signature">Daniel Reyes</p>
  </main>
</body>
</html>
```